Request for Business Card Design

Hi. My name is Marlene, I am looking for a new business card design for my company, Quarrow Signal Instruments, LLC. I really like the design you did for Tarsel Venture and was hoping you could do something similar using our full logo and our mark. I am also open to any raised texture design using our mark. I have attached our full logo, which would need to be somewhere on the card, as well as the mark in both outline and full form, as well as our brand colors / guide. The card does not have to be white, as long as our logo and mark appear. I actually like darker colored business cards more, but am open to all options. If you are interested in working with me, please let me know. We would also take the business card design into letterhead design if you can do that.

```html
<!DOCTYPE html>
<html lang="en">
<head>
<meta charset="utf-8">
<title>Quarrow Signal Instruments – Business Card</title>
<link href="https://fonts.googleapis.com/css2?family=Montserrat:wght@400;500;600;700&display=swap" rel="stylesheet">
<style>
  :root {
    --backdrop: #e9e7e4;
    --card: #1b1b1c;
    --card-edge: #111112;
    --brand-blue: #0a9ac7;
    --text-white: #f2f2f2;
    --text-muted: #cfcfcf;
  }
  * { box-sizing: border-box; margin: 0; padding: 0; }
  html, body { width: 1200px; height: 786px; overflow: hidden; }
  body {
    background: var(--backdrop);
    font-family: "Montserrat", sans-serif;
    display: flex;
    align-items: center;
    justify-content: center;
    gap: 30px;
  }
  .card {
    position: relative;
    width: 560px;
    height: 320px;
    background: var(--card);
    border: 1px solid var(--card-edge);
    overflow: hidden;
  }

  /* Wordmark */
  .wordmark {
    display: flex;
    align-items: center;
    gap: 16px;
  }
  .wordmark-dot {
    width: 58px; height: 58px;
    border-radius: 50%;
    background: var(--brand-blue);
    flex: none;
  }
  .wordmark-name {
    color: var(--text-white);
    font-weight: 700;
    font-size: 26px;
    line-height: 1.05;
    letter-spacing: 2px;
    text-transform: uppercase;
  }

  /* Front */
  .card-front .wordmark { position: absolute; left: 54px; top: 58px; }
  .holder {
    position: absolute;
    left: 54px; top: 168px;
    width: 176px;
    text-align: right;
  }
  .holder-name { color: var(--brand-blue); font-weight: 700; font-size: 24px; }
  .holder-role { color: var(--text-white); font-size: 13px; margin-top: 2px; }
  .divider {
    position: absolute;
    left: 250px; top: 160px;
    width: 2px; height: 56px;
    background: var(--brand-blue);
  }
  .contacts {
    position: absolute;
    left: 270px; top: 160px;
    list-style: none;
    color: var(--text-white);
    font-size: 12.5px;
  }
  .contacts li { display: flex; align-items: center; gap: 8px; height: 19px; }
  .contacts svg { width: 11px; height: 11px; fill: var(--brand-blue); flex: none; }
  .address-band {
    position: absolute;
    left: 0; right: 0; top: 236px;
    height: 40px;
    background: var(--brand-blue);
    display: flex;
    align-items: center;
    padding-left: 150px;
    color: var(--text-white);
    font-size: 14px;
  }
  .address-band .band-dot {
    position: absolute;
    right: 40px; top: 4px;
    width: 32px; height: 32px;
    border-radius: 50%;
    background: var(--card);
  }
  .bottom-strip {
    position: absolute;
    left: 0; right: 0; bottom: 0;
    height: 18px;
    background: var(--brand-blue);
  }

  /* Back */
  .card-back .wordmark { position: absolute; right: 40px; top: 132px; }
  .card-back .wordmark-dot { width: 44px; height: 44px; }
  .card-back .wordmark-name { font-size: 20px; }
</style>
</head>
<body>

<section class="card card-front" aria-label="Business card front">
  <div class="wordmark">
    <span class="wordmark-dot"></span>
    <span class="wordmark-name">Quarrow Signal<br>Instruments</span>
  </div>

  <div class="holder">
    <p class="holder-name">Dorian Vale</p>
    <p class="holder-role">Owner</p>
  </div>

  <span class="divider"></span>

  <ul class="contacts">
    <li>
      <svg viewBox="0 0 12 12"><path d="M2.5 1 L4.5 1 L5.3 3.6 L4 4.6 Q5 7 7.4 8 L8.4 6.7 L11 7.5 L11 9.5 Q11 11 9.5 11 Q1 10.5 1 2.5 Q1 1 2.5 1 Z"/></svg>
      +001 303 555 0142
    </li>
    <li>
      <svg viewBox="0 0 12 12"><path d="M0.5 2 H11.5 V10 H0.5 Z M1.5 3 L6 6.5 L10.5 3 Z" fill-rule="evenodd"/></svg>
      info@quarrowsignal.com
    </li>
    <li>
      <svg viewBox="0 0 12 12"><circle cx="6" cy="6" r="5.5"/></svg>
      www.quarrowsignal.com
    </li>
  </ul>

  <div class="address-band">
    1180 Ferrow Park Lane, Calder, CO 80599
    <span class="band-dot"></span>
  </div>
  <span class="bottom-strip"></span>
</section>

<section class="card card-back" aria-label="Business card back">
  <div class="wordmark">
    <span class="wordmark-dot"></span>
    <span class="wordmark-name">Quarrow Signal<br>Instruments</span>
  </div>
</section>

</body>
</html>
```